Design the Business card for NetVaultic

Business card required for a professional Cyber Security business.
Company Logo and Icon has already been provided however I would like other options for the logo and icon to compare to. Alternatively, please refine/enhance the image of the logo.icon I have already provided.

If you are going to use the provided logo and icon, I was thinking that the company raised Logo on White background would serve well on the front of the card. See attached. AND, a large company raised stand-alone icon to appear on black background on the back of the card with tagline 'Cyber Risk Management, Governance and Consulting' or 'Cyber Security for your Business' See attached.
Alternatively, provide your own design for the logo and icon.

Target Market(s)

Enterprise, Government, Financial.

Contact Information for Business Card

Tavin Orloweth
Founder and CEO

Email Address
Mobile Number
Website URL
LinkedIn URL

Logo Text

NetVaultic - see attached example of logo

Font styles to use
Other font styles liked:
• Berlin Sans FB

Requirements
Must have
• Clean large and bold icon on the back with tagline.
• Horizontal alignment,
Nice to have
• Round edges.
• Raised Logo/Icon
Should not have
• An unprofessional look and feel.

```html
<!DOCTYPE html>
<html lang="en">
<head>
<meta charset="utf-8">
<title>NetVaultic Business Card</title>
<link rel="stylesheet" href="https://fonts.googleapis.com/css2?family=Fredoka:wght@400;500&family=Roboto:wght@400&display=swap">
<style>
  :root {
    --backdrop: #2b2b2d;
    --brand-blue: #0a69b4;
    --ring-gold: #f5b400;
    --paper-white: #f2f2f2;
    --ink-white: #ffffff;
    --name-gold: #f6b51a;
    --wordmark-blue: #1f6db3;
    --back-dark: #1b1c1e;
    --tag-blue: #4f72c6;
    --tag-gold: #f5b400;
  }
  * { margin: 0; padding: 0; box-sizing: border-box; }
  html, body { width: 1200px; height: 960px; overflow: hidden; }
  body { background: var(--backdrop); position: relative; font-family: "Roboto", sans-serif; }

  .card { position: absolute; width: 600px; height: 342px; border-radius: 6px; overflow: hidden; }
  .card-front { left: 314px; top: 113px; background: var(--brand-blue); }
  .card-back { left: 311px; top: 473px; height: 340px; background: var(--back-dark); }

  .front-arc { position: absolute; inset: 0; }

  .holder { position: absolute; left: 42px; top: 103px; color: var(--ink-white); }
  .holder-name { font-family: "Fredoka", sans-serif; font-weight: 500; font-size: 20px; color: var(--name-gold); line-height: 24px; }
  .holder-role { font-family: "Fredoka", sans-serif; font-weight: 400; font-size: 14px; line-height: 18px; margin-top: 1px; }

  .contact-list { list-style: none; margin-top: 15px; }
  .contact-item { display: flex; align-items: center; font-size: 14px; line-height: 19px; }
  .contact-icon { width: 13px; height: 13px; margin-right: 10px; flex: none; }

  .wordmark { position: absolute; left: 308px; top: 151px; display: flex; align-items: center; }
  .wordmark-dot { width: 44px; height: 44px; border-radius: 50%; background: var(--wordmark-blue); margin-right: 12px; }
  .wordmark-name { font-family: "Fredoka", sans-serif; font-weight: 500; font-size: 32px; color: var(--wordmark-blue); }

  .back-mark { position: absolute; left: 0; right: 0; top: 62px; display: flex; flex-direction: column; align-items: center; }
  .back-dot { width: 120px; height: 120px; border-radius: 50%; background: var(--tag-blue); }
  .back-name { font-family: "Fredoka", sans-serif; font-weight: 500; font-size: 28px; color: var(--tag-blue); margin-top: 16px; }

  .tagline { position: absolute; left: 0; right: 0; top: 276px; text-align: center; font-family: "Fredoka", sans-serif; font-weight: 500; font-size: 17px; }
  .tagline-lead { color: var(--tag-blue); }
  .tagline-tail { color: var(--tag-gold); }
</style>
</head>
<body>
  <section class="card card-front">
    <svg class="front-arc" width="600" height="342" viewBox="0 0 600 342" aria-hidden="true">
      <circle cx="480" cy="175" r="236" fill="var(--ring-gold)"/>
      <circle cx="480" cy="175" r="231" fill="var(--brand-blue)"/>
      <circle cx="480" cy="175" r="226" fill="var(--paper-white)"/>
    </svg>

    <div class="holder">
      <p class="holder-name">Tavin Orloweth</p>
      <p class="holder-role">Founder &amp; CEO</p>
      <ul class="contact-list">
        <li class="contact-item">
          <svg class="contact-icon" viewBox="0 0 13 13"><rect x="3" y="0.5" width="7" height="12" rx="1.5" fill="none" stroke="var(--ring-gold)" stroke-width="1.5"/><circle cx="6.5" cy="10.5" r="0.8" fill="var(--ring-gold)"/></svg>
          555 201 4837
        </li>
        <li class="contact-item">
          <svg class="contact-icon" viewBox="0 0 13 13"><rect x="0.5" y="2.5" width="12" height="8" fill="var(--ring-gold)"/><path d="M0.5 2.5 L6.5 7 L12.5 2.5" fill="none" stroke="var(--brand-blue)" stroke-width="1"/></svg>
          tavin@netvaultic.com
        </li>
        <li class="contact-item">
          <svg class="contact-icon" viewBox="0 0 13 13"><circle cx="6.5" cy="6.5" r="6" fill="var(--ring-gold)"/><ellipse cx="6.5" cy="6.5" rx="2.5" ry="6" fill="none" stroke="var(--brand-blue)" stroke-width="0.9"/><line x1="0.5" y1="6.5" x2="12.5" y2="6.5" stroke="var(--brand-blue)" stroke-width="0.9"/></svg>
          www.netvaultic.com
        </li>
        <li class="contact-item">
          <svg class="contact-icon" viewBox="0 0 13 13"><circle cx="6.5" cy="6.5" r="6" fill="var(--ring-gold)"/></svg>
          netvaultic
        </li>
      </ul>
    </div>

    <div class="wordmark">
      <span class="wordmark-dot"></span>
      <span class="wordmark-name">NetVaultic</span>
    </div>
  </section>

  <section class="card card-back">
    <div class="back-mark">
      <span class="back-dot"></span>
      <span class="back-name">NetVaultic</span>
    </div>
    <p class="tagline"><span class="tagline-lead">Cyber Risk Management,</span> <span class="tagline-tail">Governance &amp; Consulting</span></p>
  </section>
</body>
</html>
```